VELTAR WEBSITE

need to create a new website for VELTAR ltd
the company deals with all aspects of safety products & safety wear
we need a simple website to show
ideas can be taken from following website whose products we shall distribute in kenya
www.kwr.co.uk
www.dorvik.eu
www.brimtoolsupplyco.com
www.gardvalewerks.co.za

we need following tabs
1) home - basic company information
2) products - broken down to following categories ie gloves, head protection, ear protection, mouth protection, foot protection
3) contacts

the company profile is a reputable company dealing with all aspects of safety, HSE (health and safety equipment), and PPE (personal protective equipment)

the website should have the dorvik logo for which we are an authorized distributor.
the dorvi industrial range writeup can be picked from their website
Updates

Dear Designers, i shall be able to choose a final design in 2 weeks, sorry i have not been able to finalise this due to a personal reason

Target Market(s)

the buyers are all types of industry who care for their employees safety

Industry/Entity Type

Industrial

Requirements
Must have
• clean look, fresh look, user freindly
Nice to have
• clear images, quick links etc

```html
<!DOCTYPE html>
<html lang="en">
<head>
<meta charset="utf-8">
<title>VELTAR – Specialized Protective &amp; Industrial Products</title>
<link href="https://fonts.googleapis.com/css2?family=Open+Sans:wght@400;600;700&display=swap" rel="stylesheet">
<style>
:root{
  --yellow:#f2b705;
  --navy:#16303d;
  --text:#6b6b6b;
  --dark:#333;
  --tile:#f2f2f2;
  --line:#d8d8d8;
}
*{box-sizing:border-box;margin:0;padding:0}
html,body{width:875px;height:1200px;overflow:hidden;background:#fff}
body{font-family:'Open Sans',Arial,sans-serif;color:var(--text);position:relative}
.abs{position:absolute}
.topbar{left:0;top:0;width:875px;height:28px;background:var(--navy);border-top:3px solid var(--yellow)}
.social{left:557px;top:3px;display:flex;height:25px}
.social span{width:30px;height:25px;border-left:1px solid #2c4654;background:#24404e;display:flex;align-items:center;justify-content:center}
.social span i{width:8px;height:8px;border-radius:50%;background:#fff;display:block}
.social .mail{background:var(--yellow);width:28px;border:0}
.logo{left:80px;top:58px;display:flex;align-items:center;gap:8px}
.logo .mark{width:26px;height:26px;background:var(--yellow)}
.logo .name{font-size:30px;font-weight:700;color:var(--navy);letter-spacing:1px}
.call{left:661px;top:48px;display:flex;gap:8px;align-items:center}
.call p{font-size:11.5px;color:var(--dark);line-height:14px}
.call p b{font-weight:400;font-size:13px}
.nav{left:404px;top:70px;height:76px;display:flex}
.nav a{font-size:11.5px;color:#555;text-decoration:none;padding:34px 0 0;height:76px}
.nav .home{background:var(--tile);border-bottom:2px solid var(--yellow);width:66px;text-align:center;color:#333}
.hero{left:0;top:147px;width:875px;height:350px;background:linear-gradient(180deg,#d8d8d6 0%,#ececea 50%,#f6f5f2 100%)}
.hero-photo{left:435px;top:0;width:440px;height:350px;background:linear-gradient(90deg,rgba(236,236,234,0) 0%,#e8c23a 35%,#c99a10 60%,#7f8a96 85%,#5d6d80 100%)}
.hero-title{left:80px;top:98px}
.hero-title .l1{background:var(--yellow);color:#fff;font-size:21px;padding:2px 12px 3px 7px;width:310px;height:31px;white-space:nowrap}
.hero-title .l2{background:var(--navy);color:#fff;font-size:21px;padding:2px 10px 3px 7px;width:222px;height:32px;white-space:nowrap}
.hero-text{left:87px;top:170px;width:300px;font-size:10px;line-height:13px;color:#555}
.hero-text p{margin-bottom:5px}
.hero-text a{display:inline-block;margin-top:8px;font-size:9px;color:#333;text-decoration:underline}
.dots{left:80px;top:497px;display:flex;gap:2px}
.dots span{width:176px;height:2px;background:#b8bcc0}
.dots .on{background:var(--yellow)}
.intro-title{left:0;top:515px;width:875px;text-align:center;font-size:22px;color:var(--navy)}
.intro-title b{color:var(--yellow);font-weight:600}
.intro-title em{color:var(--yellow);font-style:normal}
.intro-text{left:105px;top:553px;width:665px;text-align:center;font-size:10px;line-height:14.5px;color:#555}
.dash{left:80px;width:715px;border-top:1px dashed var(--line)}
.cat{top:649px;width:172px}
.cat .tile{height:102px;background:var(--tile);display:flex;flex-direction:column;align-items:center;padding-top:19px;position:relative}
.cat .tile::after{content:"";position:absolute;right:2px;bottom:2px;border-left:5px solid transparent;border-bottom:5px solid #fff}
.cat .icon{width:38px;height:38px;border-radius:50%;background:#fff;display:flex;align-items:center;justify-content:center}
.cat h3{font-size:10.5px;font-weight:600;color:#555;margin-top:15px}
.cat.active .tile{background:var(--yellow)}
.cat.active h3{color:#fff}
.cat p{font-size:10px;line-height:14.5px;text-align:center;padding:11px 12px 0;color:#777}
.heading{font-size:15px;color:var(--navy)}
.post{left:80px;width:352px;height:60px}
.post .date{width:54px;height:51px;background:var(--yellow);color:#fff;text-align:center;font-size:14px;line-height:17px;padding-top:8px;position:absolute;left:0;top:0}
.post .date b{font-weight:700}
.post .date::after{content:"";position:absolute;right:2px;bottom:2px;border-left:4px solid transparent;border-bottom:4px solid #fff}
.post .body{position:absolute;left:69px;top:0;width:280px}
.post h4{font-size:10.5px;font-weight:400;color:var(--navy);margin-bottom:6px}
.post p{font-size:10px;line-height:13.5px;color:#888}
.post a{font-size:10px;color:#555;text-decoration:none;display:block;margin-top:4px}
.quote{left:443px;top:908px;width:353px;height:178px;background:var(--tile);padding:7px 14px 0 6px;font-size:9.8px;line-height:13.2px;color:#777}
.quote .photo{float:left;width:125px;height:86px;margin-right:15px;margin-bottom:2px;background:linear-gradient(160deg,#d9d4cc 0%,#b9a89a 50%,#e7e4e0 100%)}
.quote::after{content:"";position:absolute;left:34px;bottom:-9px;border-left:0 solid transparent;border-right:12px solid transparent;border-top:9px solid var(--tile)}
.who{left:443px;top:1099px;font-size:11px;color:#333;font-family:Arial,sans-serif}
.btn{top:1122px;height:23px;font-size:8px;display:flex;align-items:center;justify-content:center;font-family:Arial,sans-serif}
.btn.dark{left:446px;width:88px;background:#8d969b;color:#fff}
.btn.light{left:550px;width:66px;background:#f0f0f0;color:#555;border:1px solid #e2e2e2}
.footer{left:0;top:1166px;width:875px;height:34px;background:var(--navy);color:#c9d1d5;font-size:9px;padding:9px 80px;display:flex;justify-content:space-between}
.footer span{color:#556a75;margin:0 6px}
</style>
</head>
<body>
<header>
  <div class="abs topbar"></div>
  <div class="abs social" aria-label="Social links">
    <span><i></i></span><span><i></i></span><span><i></i></span><span><i></i></span><span><i></i></span><span><i></i></span><span><i></i></span>
    <span class="mail"><svg width="11" height="8" viewBox="0 0 11 8"><rect x="0.5" y="0.5" width="10" height="7" fill="none" stroke="#fff"/><path d="M0.5 0.5 L5.5 4.5 L10.5 0.5" fill="none" stroke="#fff"/></svg></span>
  </div>
  <div class="abs logo"><span class="mark"></span><span class="name">VELTAR</span></div>
  <div class="abs call">
    <svg width="26" height="30" viewBox="0 0 26 30"><path d="M4 15 V11 A9 9 0 0 1 22 11 V15" fill="none" stroke="#333" stroke-width="2"/><rect x="2" y="13" width="5" height="9" rx="2" fill="#333"/><rect x="19" y="13" width="5" height="9" rx="2" fill="#333"/><path d="M21 22 Q20 27 13 27" fill="none" stroke="#333" stroke-width="1.5"/><circle cx="12" cy="27" r="1.6" fill="#333"/></svg>
    <p>Call Now<br><b>0800-5550-214-6</b></p>
  </div>
  <nav class="abs nav">
    <a class="home" href="#">Home</a>
    <a href="#" style="margin-left:13px">About Us</a>
    <a href="#" style="margin-left:31px">Our Products</a>
    <a href="#" style="margin-left:34px">Agencies</a>
    <a href="#" style="margin-left:31px">Contact Us</a>
  </nav>
</header>

<section class="abs hero">
  <div class="abs hero-photo" role="img" aria-label="Worker in yellow gloves holding a yellow hard hat, tool belt at the waist"></div>
  <div class="abs hero-title">
    <div class="l1"><b>VELTAR</b> Specialized Protective</div>
    <div class="l2">&amp; Industrial <b>Products</b></div>
  </div>
  <div class="abs hero-text">
    <p>Lorem ipsum dolor sit amet, consectetur adipisicing elit, sed do eiusmod tempor incididunt ut labore et dolore magna aliqua.</p>
    <p>Ut enim ad minim veniam, quis nostrud exercitation ullamco laboris nisi ut aliquip ex ea commodo consequat...</p>
    <a href="#">READ MORE</a>
  </div>
</section>
<div class="abs dots"><span class="on"></span><span></span><span></span></div>

<h1 class="abs intro-title" style="font-weight:400"><b>VELTAR</b> Specialized Protective <em>&amp;</em> Industrial <b>Products</b></h1>
<p class="abs intro-text">Lorem ipsum dolor sit amet, consectetur adipisicing elit, sed do eiusmod tempor incididunt ut labore et dolore magna aliqua. Ut enim ad minim veniam, quis nostrud exercitation ullamco laboris nisi ut aliquip ex ea commodo consequat. Duis aute irure dolor in reprehenderit in voluptate velit esse cillum dolore eu fugiat nulla pariatur.</p>
<div class="abs dash" style="top:626px"></div>

<div class="abs cat active" style="left:80px">
  <div class="tile"><span class="icon"><svg width="24" height="18" viewBox="0 0 24 18"><path d="M3 13 A9 9 0 0 1 21 13 Z" fill="#555"/><rect x="1" y="13" width="22" height="3" rx="1.5" fill="#555"/></svg></span><h3>HEAD PROTECTION</h3></div>
  <p>Lorem ipsum dolor sit amet, consectetur adipisicing elit, sed do eiusmod tempor incididunt magna aliqua.</p>
</div>
<div class="abs cat" style="left:261px">
  <div class="tile"><span class="icon"><svg width="18" height="24" viewBox="0 0 18 24"><rect x="4" y="3" width="2.6" height="11" rx="1.3" fill="#555"/><rect x="7.4" y="1" width="2.6" height="13" rx="1.3" fill="#555"/><rect x="10.8" y="2" width="2.6" height="12" rx="1.3" fill="#555"/><rect x="14" y="4" width="2.4" height="10" rx="1.2" fill="#555"/><path d="M4 12 H16.4 V17 Q16 23 10 23 Q5 23 2 16 L1 12 Q2 11 4 13 Z" fill="#555"/></svg></span><h3>HAND PROTECTION</h3></div>
  <p>Lorem ipsum dolor sit amet, consectetur adipisicing elit, sed do eiusmod tempor incididunt magna aliqua.</p>
</div>
<div class="abs cat" style="left:442px">
  <div class="tile"><span class="icon"><svg width="26" height="16" viewBox="0 0 26 16"><path d="M2 2 H10 V7 L20 9 Q24 10 24 13 H2 Z" fill="#555"/><rect x="2" y="13.5" width="22" height="2" fill="#555"/></svg></span><h3>FOOT PROTECTION</h3></div>
  <p>Lorem ipsum dolor sit amet, consectetur adipisicing elit, sed do eiusmod tempor incididunt magna aliqua.</p>
</div>
<div class="abs cat" style="left:623px">
  <div class="tile"><span class="icon"><svg width="24" height="26" viewBox="0 0 24 26"><path d="M10 23 Q13 24 14 20 Q15 16 18 13 Q21 9 18 4 Q14 0 9 3 Q7 5 7 8" fill="none" stroke="#555" stroke-width="2"/><path d="M11 9 Q13 6 15 9 Q16 12 13 14" fill="none" stroke="#555" stroke-width="1.6"/><path d="M1 14 H8 M5 11 L8 14 L5 17" fill="none" stroke="#555" stroke-width="2"/></svg></span><h3>EAR PROTECTION</h3></div>
  <p>Lorem ipsum dolor sit amet, consectetur adipisicing elit, sed do eiusmod tempor incididunt magna aliqua.</p>
</div>
<div class="abs dash" style="top:842px"></div>

<h2 class="abs heading" style="left:80px;top:858px;font-weight:400">Latest From The Blog</h2>
<div class="abs dash" style="top:893px;width:352px"></div>
<article class="abs post" style="top:912px"><div class="date">Nov<br><b>02</b></div><div class="body"><h4>Lorem Ipsum Dolor Sit Amet</h4><p>Lorem ipsum dolor sit amet, consectetur adipisicing elit, sed do eiusmod tempor incididunt magna aliqua...</p><a href="#">Read More</a></div></article>
<div class="abs dash" style="top:979px;width:352px"></div>
<article class="abs post" style="top:994px"><div class="date">Nov<br><b>02</b></div><div class="body"><h4>Lorem Ipsum Dolor Sit Amet</h4><p>Lorem ipsum dolor sit amet, consectetur adipisicing elit, sed do eiusmod tempor incididunt magna aliqua...</p><a href="#">Read More</a></div></article>
<div class="abs dash" style="top:1062px;width:352px"></div>
<article class="abs post" style="top:1076px"><div class="date">Nov<br><b>02</b></div><div class="body"><h4>Lorem Ipsum Dolor Sit Amet</h4><p>Lorem ipsum dolor sit amet, consectetur adipisicing elit, sed do eiusmod tempor incididunt magna aliqua...</p><a href="#">Read More</a></div></article>
<div class="abs dash" style="top:1145px;width:352px"></div>

<h2 class="abs heading" style="left:443px;top:858px;font-weight:400">Our Client Say</h2>
<div class="abs dash" style="top:893px;left:443px;width:353px"></div>
<blockquote class="abs quote">
  <div class="photo" role="img" aria-label="Portrait photo of the client"></div>
  <p style="padding-top:11px">Lorem ipsum dolor sit amet, consectetur adipisicing elit, sed do eiusmod tempor incididunt ut labore et dolore magna aliqua. Ut enim ad minim veniam, quis nostrud exercitation ullamco laboris nisi ut aliquip ex ea commodo consequat. Duis aute irure dolor in reprehenderit in voluptate velit esse cillum dolore eu fugiat nulla pariatur. Excepteur sint occaecat cupidatat non proident, sunt in culpa qui officia deserunt mollit anim id est laborum. Lorem ipsum dolor sit amet, consectetur adipisicing elit, sed do eiusmod tempor incididunt ut labore et dolore magna aliqua....</p>
</blockquote>
<p class="abs who"><b>Mara K.</b>, CEO, Fieldcrest Supply LLC.</p>
<a class="abs btn dark" href="#">ALL TESTIMONIALS</a>
<a class="abs btn light" href="#">OUR WORKS</a>

<footer class="abs footer">
  <div>© Copyrights 2013 All rights Reserved</div>
  <div>Privacy Policy<span>|</span>Terms Of Uses</div>
</footer>
</body>
</html>
```